PowerPoint Listing Presentation for Real Estate Agency

We need a PowerPoint presentation for a new real estate brokerage team.

[[[[[[submit 1-3 sample slides for review - i will provide feedback and you can make changes if you want to - we will not be deciding on a design prior to the deadline]]]]]

******ATTN: DESIGNERS, if your skills are webdesign then just look at this like a portable website or a brochure. it should be easy enough******

NOTE: we have all the data to put into the slides. You just need to come up with the design and layout. we have a sample design that we like and have provided.

This focus will be for the home listing side of the business (a presentation for home sellers to convince them to use our services). The data and slides will present our team and the benefits, in the best light, to use our services over that of other real estate agent applying for the job. This presentation will proved facts and benefits and describe our special and unique offerings that will show a home seller why we can sell their home for more money in less time and with the least amount of hassle. The main color scheme is Dark Blue and White (we want some additional colors included - based on your creativity. otherwise the presentation will too monotone). We would like to see the use of Statistical Graphs (3-D) - data provided. We have photos of our team and a new logo (the logo could have some minor adjustment to clean it up if necessary) - also uploaded. We have about 80-90% of the information that will be put into the slides and will need to work closely to get the design and data integrated into the presentation (should be easier then it sounds). We should be able to add slides and data 'at will' over time via our master slides built into the presentation. We have a pretty good sample presentation that we like and can be used as a guideline (this is from our affiliated business network and we have full rights to all the information), it is uploaded but doesn't contain all the slide because of size limitations.

NOTE: An additional buyers presentation will be needed after we get the sellers presentation completed, which means additional work.

This should be enough to get you started and we are available if you have any questions to help you with the project. there will be around 60-70 total slides. once concept is completed it will be easy to create the slides.

Target Market(s)

home sellers. people who are moving to a new and better home or relocation for job reasons. typically more established in life

Industry/Entity Type

Real Estate

Requirements
Must have
• all the slides must be congruent. in other words, the exact same layout feel should used across the board. we are working on building our trade dress/image. Also, it must have a soft and inviting overall feel, yet show strength of ability.
Nice to have
• nice to have use of real people images when necessary. 3D graphs would be nice. clean modern look and feel, yet sophisticated and professional.
Should not have
• should not have a lot of time consuming transitions. do not include 3D stick figures or distracting moving gifs

```html
<!DOCTYPE html>
<html lang="en">
<head>
<meta charset="utf-8">
<title>Project Slide</title>
<link href="https://fonts.googleapis.com/css2?family=Open+Sans:wght@400;700&family=Roboto+Condensed:wght@700&display=swap" rel="stylesheet">
<style>
  :root {
    --navy: #191a5c;
    --title-blue: #1f4f9e;
    --bullet-blue: #3b63d6;
    --body-grey: #4a4a4a;
    --copyright: #a3a3ee;
    --page-ink: #111111;
    --paper: #ffffff;
  }
  * { margin: 0; padding: 0; box-sizing: border-box; }
  html, body { width: 1200px; height: 900px; overflow: hidden; background: var(--paper); }
  .slide {
    position: relative;
    width: 1200px;
    height: 900px;
    overflow: hidden;
    font-family: "Open Sans", Arial, sans-serif;
    background: linear-gradient(160deg, #ededf0 0%, #fafafb 40%, #f4f4f6 75%, #ececef 100%);
  }
  .top-bar {
    position: absolute; left: 0; top: 0; width: 1200px; height: 52px;
    background: var(--navy);
  }
  .brand {
    position: absolute; right: 22px; top: 0; height: 52px;
    display: flex; align-items: center; gap: 10px;
    color: var(--paper); font-weight: 700; font-size: 20px; letter-spacing: 0.5px;
  }
  .brand-square { width: 14px; height: 14px; background: var(--paper); }
  .slide-title {
    position: absolute; left: 57px; top: 112px;
    font-size: 41px; font-weight: 400; color: var(--title-blue);
  }
  .section-heading {
    font-size: 32px; font-weight: 700; color: var(--title-blue);
    line-height: 38px; height: 38px;
  }
  .column-left { position: absolute; left: 57px; top: 221px; width: 510px; }
  .body-copy {
    margin: 11px 0 0 3px;
    font-size: 23px; line-height: 36px; color: var(--body-grey);
  }
  .body-copy .line { display: block; text-align: justify; text-align-last: justify; white-space: nowrap; }
  .body-copy .line-end { display: block; text-align: left; white-space: nowrap; }
  .heading-second { margin-top: 23px; }
  .heading-second + .body-copy { margin-top: 9px; }
  .divider {
    position: absolute; left: 603px; top: 255px; width: 2px; height: 555px;
    background: linear-gradient(180deg, rgba(160,160,170,0), rgba(150,150,160,0.8) 40%, rgba(150,150,160,0.8) 70%, rgba(160,160,170,0));
  }
  .column-right { position: absolute; left: 644px; top: 224px; width: 520px; }
  .feature-list { list-style: none; margin-top: 6px; }
  .feature-list li {
    display: flex; align-items: center; height: 61.5px;
    font-size: 27px; color: var(--body-grey);
  }
  .feature-list .chevrons { width: 46px; flex: none; padding-left: 6px; }
  .footer-band { position: absolute; left: 0; top: 815px; width: 1200px; height: 85px; }
  .page-number {
    position: absolute; left: 37px; top: 840px;
    font-family: "Roboto Condensed", "Arial Narrow", sans-serif;
    font-weight: 700; font-size: 24px; color: var(--page-ink);
  }
  .copyright {
    position: absolute; left: 268px; top: 844px;
    font-size: 22px; color: var(--copyright);
  }
</style>
</head>
<body>
<main class="slide">
  <header class="top-bar">
    <div class="brand"><span class="brand-square"></span>Harlow &amp; Vance</div>
  </header>

  <h1 class="slide-title">Project Title Here</h1>

  <section class="column-left">
    <h2 class="section-heading">Heading 1</h2>
    <p class="body-copy">
      <span class="line">Lorem ipsum dolor sit ipsum Lorem ipsum</span>
      <span class="line">dolor sit ipsum Lorem ipsum dolor sit ipsum</span>
      <span class="line">Lorem ipsum dolor sit ipsum Lorem ipsum</span>
      <span class="line">dolor sit ipsum Lorem ipsum dolor sit ipsum</span>
      <span class="line">Lorem ipsum dolor sit ipsum Lorem ipsum</span>
      <span class="line-end">dolor sit ipsum Lorem ipsum</span>
    </p>
    <h2 class="section-heading heading-second">Heading 2</h2>
    <p class="body-copy">
      <span class="line">Lorem ipsum dolor sit ipsum Lorem ipsum</span>
      <span class="line">dolor sit ipsum Lorem ipsum dolor sit ipsum</span>
      <span class="line">Lorem ipsum dolor sit ipsum Lorem ipsum</span>
      <span class="line">dolor sit ipsum Lorem ipsum dolor sit ipsum</span>
      <span class="line-end">Lorem ipsum dolor sit</span>
    </p>
  </section>

  <div class="divider"></div>

  <section class="column-right">
    <h2 class="section-heading">Heading 3</h2>
    <ul class="feature-list">
      <li><svg class="chevrons" width="46" height="20" viewBox="0 0 46 20" aria-hidden="true"><path d="M6 5 L11 10 L6 15 M13 5 L18 10 L13 15" fill="none" stroke="var(--bullet-blue)" stroke-width="3"/></svg>Lorem ipsum dolor sit ipsum</li>
      <li><svg class="chevrons" width="46" height="20" viewBox="0 0 46 20" aria-hidden="true"><path d="M6 5 L11 10 L6 15 M13 5 L18 10 L13 15" fill="none" stroke="var(--bullet-blue)" stroke-width="3"/></svg>Lorem ipsum dolor sit ipsum</li>
      <li><svg class="chevrons" width="46" height="20" viewBox="0 0 46 20" aria-hidden="true"><path d="M6 5 L11 10 L6 15 M13 5 L18 10 L13 15" fill="none" stroke="var(--bullet-blue)" stroke-width="3"/></svg>Lorem ipsum dolor sit ipsum</li>
      <li><svg class="chevrons" width="46" height="20" viewBox="0 0 46 20" aria-hidden="true"><path d="M6 5 L11 10 L6 15 M13 5 L18 10 L13 15" fill="none" stroke="var(--bullet-blue)" stroke-width="3"/></svg>Lorem ipsum dolor sit ipsum</li>
      <li><svg class="chevrons" width="46" height="20" viewBox="0 0 46 20" aria-hidden="true"><path d="M6 5 L11 10 L6 15 M13 5 L18 10 L13 15" fill="none" stroke="var(--bullet-blue)" stroke-width="3"/></svg>Lorem ipsum dolor sit ipsum</li>
      <li><svg class="chevrons" width="46" height="20" viewBox="0 0 46 20" aria-hidden="true"><path d="M6 5 L11 10 L6 15 M13 5 L18 10 L13 15" fill="none" stroke="var(--bullet-blue)" stroke-width="3"/></svg>Lorem ipsum dolor sit ipsum</li>
      <li><svg class="chevrons" width="46" height="20" viewBox="0 0 46 20" aria-hidden="true"><path d="M6 5 L11 10 L6 15 M13 5 L18 10 L13 15" fill="none" stroke="var(--bullet-blue)" stroke-width="3"/></svg>Lorem ipsum dolor sit ipsum</li>
      <li><svg class="chevrons" width="46" height="20" viewBox="0 0 46 20" aria-hidden="true"><path d="M6 5 L11 10 L6 15 M13 5 L18 10 L13 15" fill="none" stroke="var(--bullet-blue)" stroke-width="3"/></svg>Lorem ipsum dolor sit ipsum</li>
    </ul>
  </section>

  <svg class="footer-band" width="1200" height="85" viewBox="0 0 1200 85" aria-hidden="true">
    <path d="M147 85 L203 20 Q222 2 252 2 L1200 2 L1200 85 Z" fill="var(--navy)"/>
  </svg>
  <div class="page-number">Page : 02</div>
  <div class="copyright">Copyright text here</div>
</main>
</body>
</html>
```